Business card design for my company.
I would like the card's background colour to be black. You can also see our web site to get an idea of our brand. https://www.tmwhomecrafting.com.au/
- Name
- Email

```html
<!DOCTYPE html>
<html lang="en">
<head>
<meta charset="utf-8">
<title>TMW Home Crafting — Business Card</title>
<link href="https://fonts.googleapis.com/css2?family=Arimo:wght@400;700&display=swap" rel="stylesheet">
<style>
  :root {
    --backdrop: #e4e4e4;
    --card: #2f2f2f;
    --brand-green: #0f9447;
    --ink-light: #ffffff;
    --divider: #6a6a6a;
  }
  * { margin: 0; padding: 0; box-sizing: border-box; }
  html, body {
    width: 1200px; height: 1200px; overflow: hidden;
    background: var(--backdrop);
    font-family: "Arimo", Arial, sans-serif;
  }
  .card {
    position: absolute;
    left: 255px;
    width: 690px; height: 393px;
    background: var(--card);
    color: var(--ink-light);
  }
  .card--front { top: 158px; }
  .card--back { top: 653px; }

  .brand {
    position: absolute;
    display: flex; align-items: center; gap: 12px;
  }
  .brand__mark {
    width: 16px; height: 16px;
    background: var(--brand-green);
    flex: none;
  }
  .brand__name {
    font-weight: 700;
    color: var(--ink-light);
    letter-spacing: 1px;
    line-height: 1.1;
    text-transform: uppercase;
  }
  .card--front .brand { left: 82px; top: 168px; }
  .card--front .brand__name { font-size: 28px; }
  .card--back .brand {
    left: 50%; top: 50%;
    transform: translate(-50%, -50%);
    gap: 18px;
  }
  .card--back .brand__mark { width: 26px; height: 26px; }
  .card--back .brand__name { font-size: 46px; }

  .divider {
    position: absolute;
    left: 376px; top: 75px;
    width: 1px; height: 229px;
    background: linear-gradient(to bottom, transparent, var(--divider) 15%, var(--divider) 85%, transparent);
  }

  .contact {
    position: absolute;
    left: 402px; top: 86px;
    font-size: 16px;
    line-height: 1.3;
  }
  .contact__name {
    color: var(--brand-green);
    font-weight: 700;
    font-size: 26px;
    line-height: 1;
  }
  .contact__role { font-size: 15px; margin-top: 6px; }
  .contact__address { margin-top: 26px; line-height: 21px; }
  .contact__list { list-style: none; margin-top: 12px; }
  .contact__item {
    display: flex; align-items: center;
    height: 20.5px;
  }
  .contact__icon {
    width: 14px; height: 14px;
    margin-right: 12px;
    fill: var(--brand-green);
    flex: none;
  }
</style>
</head>
<body>

<section class="card card--front">
  <div class="brand">
    <span class="brand__mark"></span>
    <span class="brand__name">TMW Home<br>Crafting</span>
  </div>

  <div class="divider"></div>

  <div class="contact">
    <div class="contact__name">DANIEL REYES</div>
    <div class="contact__role">President</div>
    <div class="contact__address">412 Wattle Grove Road<br>Ballarat, Victoria 3350</div>
    <ul class="contact__list">
      <li class="contact__item">
        <svg class="contact__icon" viewBox="0 0 24 24"><path d="M6.6 10.8a15.1 15.1 0 0 0 6.6 6.6l2.2-2.2c.3-.3.7-.4 1-.2 1.1.4 2.3.6 3.6.6.6 0 1 .4 1 1V20c0 .6-.4 1-1 1A17 17 0 0 1 3 4c0-.6.4-1 1-1h3.5c.6 0 1 .4 1 1 0 1.3.2 2.5.6 3.6.1.3 0 .7-.2 1z"/></svg>
        555-214-7730
      </li>
      <li class="contact__item">
        <svg class="contact__icon" viewBox="0 0 24 24"><path d="M7 1h10a2 2 0 0 1 2 2v18a2 2 0 0 1-2 2H7a2 2 0 0 1-2-2V3a2 2 0 0 1 2-2zm0 3v15h10V4zm5 16.2a1 1 0 1 0 0 .01z"/></svg>
        555-390-1846
      </li>
      <li class="contact__item">
        <svg class="contact__icon" viewBox="0 0 24 24"><path d="M2 5h20v14H2zm2 2v.4l8 5.3 8-5.3V7zm0 2.8V17h16V9.8l-8 5.3z"/></svg>
        info@tmwhome.com
      </li>
      <li class="contact__item">
        <svg class="contact__icon" viewBox="0 0 24 24"><circle cx="12" cy="12" r="10"/></svg>
        www.tmwhome.com
      </li>
    </ul>
  </div>
</section>

<section class="card card--back">
  <div class="brand">
    <span class="brand__mark"></span>
    <span class="brand__name">TMW Home Crafting</span>
  </div>
</section>

</body>
</html>
```